Emberline Air Business Card Design

Design new, 2 sides, business cards for a residential and light commercial heating, air conditioning contractor.

Target Market(s)

Homeowners, small businesses

Industry/Entity Type

Business

Contact Information for Business Card

Dominic Westerhall
Phone - 862-415-2736
Email
Address - PO box 518
Brightwater NJ 07912
Website - www.HarborBreezeLLC.example

Requirements
Must have
• logo, company colors, standard size with no die cut, so I can use nova stamp

```html
<!DOCTYPE html>
<html lang="en">
<head>
<meta charset="utf-8">
<title>Emberline Air Business Card</title>
<link rel="stylesheet" href="https://fonts.googleapis.com/css2?family=Arimo:wght@400;700&display=swap">
<style>
  :root {
    --stage: #3a3a3a;
    --brand-red: #9c1f35;
    --brand-orange: #f5a623;
    --cream: #fbeed2;
    --card-white: #ffffff;
    --text-grey: #6b6b6b;
  }
  * { margin: 0; padding: 0; box-sizing: border-box; }
  html, body { width: 1200px; height: 950px; overflow: hidden; }
  body {
    background: var(--stage);
    font-family: "Arimo", Arial, sans-serif;
    position: relative;
  }
  .card {
    position: absolute;
    left: 250px;
    width: 700px;
    height: 400px;
    overflow: hidden;
    box-shadow: 0 8px 24px rgba(0,0,0,0.45);
  }
  .card-front {
    top: 55px;
    background: var(--brand-red);
    display: flex;
    align-items: center;
    justify-content: center;
  }
  .brand-name {
    font-family: "Arimo", Arial, sans-serif;
    font-weight: 700;
    text-transform: uppercase;
    letter-spacing: 2px;
  }
  .card-front .brand-name { color: var(--cream); font-size: 52px; }

  .card-back { top: 495px; background: var(--card-white); }
  .accent-left {
    position: absolute; left: 0; top: 175px; width: 9px; height: 225px;
    background: var(--brand-orange); border-top-right-radius: 9px;
  }
  .accent-bottom {
    position: absolute; left: 0; bottom: 0; width: 150px; height: 6px;
    background: var(--brand-orange);
  }
  .accent-right {
    position: absolute; right: 0; top: 0; width: 9px; height: 225px;
    background: var(--brand-orange); border-bottom-left-radius: 9px;
  }
  .accent-top {
    position: absolute; right: 0; top: 0; width: 150px; height: 6px;
    background: var(--brand-orange);
  }
  .contact-block { position: absolute; left: 55px; top: 150px; }
  .person-name { color: var(--brand-red); font-weight: 700; font-size: 22px; text-transform: uppercase; }
  .person-title { color: var(--brand-orange); font-size: 17px; text-transform: uppercase; margin-top: 3px; }
  .address { color: var(--text-grey); font-size: 15px; line-height: 20px; margin-top: 22px; }
  .contact-list { list-style: none; margin-top: 14px; }
  .contact-list li {
    display: flex; align-items: center; gap: 10px;
    color: var(--text-grey); font-size: 15px; line-height: 21px;
  }
  .contact-list svg { width: 13px; height: 13px; fill: var(--brand-red); flex: none; }
  .card-back .brand-name {
    position: absolute; right: 55px; top: 120px; width: 270px;
    text-align: center; color: var(--brand-red); font-size: 36px; line-height: 44px;
  }
</style>
</head>
<body>
  <section class="card card-front" aria-label="Card front">
    <div class="brand-name">Emberline Air</div>
  </section>

  <section class="card card-back" aria-label="Card back">
    <div class="accent-left"></div>
    <div class="accent-bottom"></div>
    <div class="accent-right"></div>
    <div class="accent-top"></div>

    <div class="contact-block">
      <div class="person-name">Dominic Westerhall</div>
      <div class="person-title">President</div>
      <div class="address">PO box 518<br>Brightwater NJ 07912</div>
      <ul class="contact-list">
        <li><svg viewBox="0 0 16 16"><path d="M3 1l3 3-2 2c1 2 4 5 6 6l2-2 3 3-2 3C7 15 1 9 1 3z"/></svg>862-415-2736</li>
        <li><svg viewBox="0 0 16 16"><path d="M4 0h8v16H4zM5.5 2v10h5V2z"/></svg>862-415-2790</li>
        <li><svg viewBox="0 0 16 16"><path d="M4 0h8v5H4zM1 6h14v8h-3v2H4v-2H1zM5 11v3h6v-3z"/></svg>862-415-2791</li>
        <li><svg viewBox="0 0 16 16"><path d="M0 3h16v10H0zM1.5 4.5L8 9l6.5-4.5z"/></svg>dominic@emberlineair.example</li>
        <li><svg viewBox="0 0 16 16"><circle cx="8" cy="8" r="8"/></svg>www.EmberlineAirLLC.example</li>
      </ul>
    </div>

    <div class="brand-name">Emberline Air</div>
  </section>
</body>
</html>
```